Brimlow OrthoLink IT Inc. new website

i need a website for my company which is dedicated to installation and service of computer systems in Dental Offices. I would like for it to encompass a technology feel and professional look. The company deals with all aspects of technology like, Audio Visual, computer systems and networks, Cloud services like data backup, data center. We provide manage services, support and services to Dental Professionals.
Updates

Looking for a Technology font but professional look Added Wednesday, April 20, 2016

Target Market(s)

Dental, Dentist

Industry/Entity Type

Dental

Number of Pages Required

5+ page

Font styles to use
Other font styles liked:
• Futuristic or Techy

Colors
0255a3
ec1f27

Requirements
Must have
• Tabs
Nice to have
• Have no idea maybe some suggestion on your part may help
Should not have
• A professional feel but have a techy look

```html
<!DOCTYPE html>
<html lang="en">
<head>
<meta charset="utf-8">
<title>Brimlow OrthoLink IT Inc.</title>
<link href="https://fonts.googleapis.com/css2?family=Exo+2:wght@600;700&family=Lato:wght@400;700&family=Michroma&family=Oswald:wght@500&display=swap" rel="stylesheet">
<style>
:root{
  --blue:#0255a3;
  --blue-bright:#0a7fc8;
  --sky:#1e90e0;
  --ink:#111;
  --body:#333;
  --light:#f1f1f1;
  --rule:#cfcfcf;
  --panel:#d9d9d9;
  --panel-edge:#c4c4c4;
  --footer-deep:#222;
  --footer-text:#e6e6e6;
  --field:#1f1f1f;
  --quote-mark:#cfcfcf;
}
*{box-sizing:border-box;margin:0;padding:0}
html,body{width:1200px;height:2473px;overflow:hidden}
body{position:relative;background:#fff;font-family:"Lato",sans-serif;color:var(--body)}
.abs{position:absolute}

.topbar{left:0;top:0;width:1200px;height:38px;background:var(--blue-bright)}
.topbar-phone{left:790px;top:6px;color:#fff;font:700 18px "Lato",sans-serif;display:flex;align-items:center;gap:8px}
.social{display:flex;gap:6px}
.social span{width:26px;height:26px;background:#fff;border:2px solid var(--blue);display:block}
.topbar .social{position:absolute;left:962px;top:6px}

.header{left:0;top:38px;width:1200px;height:115px;background:#fff}
.brand{left:132px;top:37px;display:flex;align-items:center;gap:10px;font:700 27px "Exo 2",sans-serif;color:var(--blue)}
.brand i{width:34px;height:34px;background:var(--blue);display:block}
.nav{left:462px;top:40px;display:flex;align-items:center;font:12.5px "Michroma",sans-serif;color:#111;-webkit-text-stroke:.4px currentColor}
.nav a{color:inherit;text-decoration:none;padding:0 24px;border-left:1px solid #9cc6e8;line-height:22px}
.nav .home{border:none;padding:0 20px 0 0}

.hero{left:0;top:153px;width:1200px;height:501px;background:linear-gradient(90deg,#071428 0%,#0c2a4e 35%,#2b5a7d 55%,#6f94aa 80%,#9bb6c4 100%)}
.hero-title{left:585px;top:200px;font:500 35px/46px "Oswald",sans-serif;color:#fff;text-shadow:0 2px 4px rgba(0,0,0,.45)}
.hero-next{left:1118px;top:210px}

.title{width:1200px;left:0;text-align:center;font:27px "Michroma",sans-serif;color:var(--ink);-webkit-text-stroke:.8px currentColor}
.title b{font-weight:400;color:var(--blue)}
.divider{left:376px;width:448px;height:16px}
.divider:before{content:"";position:absolute;left:0;right:0;top:8px;border-top:1px solid var(--rule)}
.divider i{position:absolute;left:214px;top:0;width:20px;height:16px;background:#8a8a8a;border:3px solid #fff;outline:1px solid #bbb}

.welcome-text{left:148px;top:788px;width:907px;text-align:center;font:14.5px/26px "Lato",sans-serif}
.btn-more{left:527px;top:918px;width:147px;height:36px;background:var(--blue-bright);border-radius:4px;color:#fff;font:700 14px "Exo 2",sans-serif;display:flex;align-items:center;overflow:hidden}
.btn-more span{flex:1;text-align:center}
.btn-more em{width:40px;height:100%;background:var(--sky);display:flex;align-items:center;justify-content:center}

.services{left:0;top:1002px;width:1200px;height:531px;background:var(--light)}
.svc-bar{top:1313px;height:12px;width:300px;background:#dedede}
.svc-panel{left:481px;top:1208px;width:244px;height:180px;background:var(--panel);border:2px solid var(--panel-edge)}
.svc-icon{width:99px;height:96px;background:linear-gradient(180deg,#1b8ee0,#0255a3);border:3px solid #fff;box-shadow:0 1px 4px rgba(0,0,0,.3);display:flex;align-items:center;justify-content:center}
.svc h3{font:700 22px/27px "Exo 2",sans-serif;color:var(--blue)}
.svc p{font:14px/18px "Lato",sans-serif;color:#222;margin-top:3px}
.svc.left{text-align:right;width:330px}
.svc.right{width:330px}

.quote{left:140px;top:1676px;width:920px;text-align:center;font:17px/31px "Lato",sans-serif;color:#222}
.qmark{font:64px/0 Georgia,serif;color:var(--quote-mark);vertical-align:-24px;margin:0 6px}
.author{left:0;top:1793px;width:1200px;text-align:center;font:700 17px "Lato",sans-serif;color:var(--blue)}
.client{background:linear-gradient(180deg,#b5b5b5,#6d6d6d);border:4px solid #ccc}
.client.active{border:6px solid var(--blue);background:linear-gradient(180deg,#c9c9c9,#7a8aa0)}

.footer{left:0;top:2052px;width:1200px;height:371px;background:radial-gradient(ellipse at 50% 20%,#3b3b3b,#262626)}
.f-head{top:2095px;font:600 19px "Exo 2",sans-serif;color:#fff;padding-bottom:12px;border-bottom:1px solid #555}
.f-links{left:135px;top:2156px;list-style:none;font:14.5px/42px "Lato",sans-serif;color:var(--footer-text)}
.f-links li:before{content:"›";margin-right:8px;font-weight:700}
.f-vr{top:2098px;width:2px;height:270px;background:#1c1c1c;border-right:1px solid #444}
.f-contact{left:340px;font:14.5px/22px "Lato",sans-serif;color:var(--footer-text);display:flex;gap:14px}
.f-contact strong{font-weight:700}
.field{left:626px;width:242px;height:28px;background:var(--field);color:#999;font:13px/28px "Lato",sans-serif;padding-left:12px}
.submit{left:626px;top:2348px;width:94px;height:35px;background:var(--blue);color:#fff;font:700 17px/35px "Lato",sans-serif;text-align:center}
.f-brand{left:920px;top:2160px;width:172px;text-align:center;font:700 22px/28px "Exo 2",sans-serif;color:#7a7a7a}
.f-brand i{display:block;width:40px;height:40px;margin:0 auto 10px;background:#6a6a6a}
.footer-social{left:952px;top:2307px}
.copyright{left:0;top:2423px;width:1200px;height:50px;background:var(--footer-deep);color:#ddd;font:13px/50px "Lato",sans-serif;text-align:center}
</style>
</head>
<body>

<div class="abs topbar">
  <div class="abs topbar-phone">
    <svg width="22" height="22" viewBox="0 0 22 22"><circle cx="11" cy="11" r="10" fill="none" stroke="#fff" stroke-width="1.6"/><path d="M7.5 6c1 0 1.5 2 1.2 2.6l-.8.8c.6 1.4 1.8 2.6 3.2 3.2l.8-.8c.6-.3 2.6.2 2.6 1.2 0 1-1 2-2 2-3.6-.3-6.6-3.3-7-7 0-1 1-2 2-2z" fill="#fff"/></svg>
    555-014-2290
  </div>
  <div class="social"><span></span><span></span><span></span></div>
</div>

<header class="abs header">
  <div class="abs brand"><i></i>Brimlow OrthoLink IT</div>
  <nav class="abs nav">
    <a class="home" href="#"><svg width="30" height="26" viewBox="0 0 30 26"><path d="M15 2 2 13h4v11h7v-7h4v7h7V13h4z" fill="var(--blue-bright)"/></svg></a>
    <a href="#">ABOUT US</a><a href="#">SERVICES</a><a href="#">SUPPORT</a><a href="#">CONTACT US</a>
  </nav>
</header>

<section class="abs hero" role="img" aria-label="Hand touching a glowing IT interface beside a modern dental treatment room">
  <h1 class="abs hero-title">We Provide Manage Services, Support<br>&amp; Service To Dental Professionals.</h1>
  <svg class="abs hero-next" width="30" height="80" viewBox="0 0 30 80"><path d="M4 4 26 40 4 76" fill="none" stroke="var(--sky)" stroke-width="4"/></svg>
</section>

<section>
  <h2 class="abs title" style="top:700px">Welcome To <b>Brimlow OrthoLink IT</b></h2>
  <div class="abs divider" style="top:757px"><i></i></div>
  <p class="abs welcome-text">Lorem ipsum dolor sit amet, consectetuer adipiscing elit, sed diam nonummy nibh euismod tincidunt ut laoreet dolore magna aliquam erat volutpat. Ut wisi enim ad minim veniam, quis nostrud exerci tation ullamcorper suscipit lobortis nisl ut aliquip ex ea commodo consequat. Duis autem vel eum iriure dolor in hendrerit in vulputate velit esse molestie consequat, vel illum dolore feugiat nulla facilisis at vero eros et accumsan et iusto odio dignissim qui blandit praesent luptatum zzril facilisi.</p>
  <a class="abs btn-more"><span>Read More</span><em><svg width="22" height="12" viewBox="0 0 22 12"><path d="M0 6h20M15 1l5 5-5 5" fill="none" stroke="#fff" stroke-width="2"/></svg></em></a>
</section>

<section class="abs services"></section>
<h2 class="abs title" style="top:1050px">Our <b>Services</b></h2>
<div class="abs divider" style="top:1108px"><i></i></div>
<div class="abs svc-bar" style="left:132px"></div>
<div class="abs svc-bar" style="left:768px"></div>
<div class="abs svc-panel" role="img" aria-label="Central technology graphic"></div>

<div class="abs svc-icon" style="left:433px;top:1154px"><svg width="56" height="48" viewBox="0 0 56 48"><path d="M4 16h10l14-12v40L14 32H4z" fill="#fff"/><path d="M36 14q6 10 0 20M42 8q11 16 0 32" fill="none" stroke="#fff" stroke-width="4"/></svg></div>
<div class="abs svc-icon" style="left:669px;top:1154px"><svg width="56" height="56" viewBox="0 0 56 56"><rect x="4" y="4" width="20" height="48" fill="#fff"/><rect x="8" y="10" width="12" height="4" fill="#1a7fd0"/><rect x="8" y="20" width="12" height="4" fill="#1a7fd0"/><path d="M24 14h10v28H24M34 28h6" fill="none" stroke="#fff" stroke-width="3"/><rect x="40" y="6" width="12" height="12" fill="#fff"/><rect x="40" y="38" width="12" height="12" fill="#fff"/><path d="M34 12h6M34 44h6" stroke="#fff" stroke-width="3"/></svg></div>
<div class="abs svc-icon" style="left:433px;top:1389px"><svg width="58" height="50" viewBox="0 0 58 50"><path d="M14 26a9 9 0 0 1 3-17 12 12 0 0 1 23-1 9 9 0 0 1 6 18z" fill="#fff"/><path d="M24 18l5-5 5 5M29 13v10" stroke="#1a7fd0" stroke-width="3" fill="none"/><rect x="6" y="32" width="46" height="14" rx="3" fill="#fff"/><circle cx="44" cy="39" r="2.5" fill="#1a7fd0"/></svg></div>
<div class="abs svc-icon" style="left:669px;top:1389px"><svg width="54" height="54" viewBox="0 0 54 54"><path d="M12 26a15 15 0 0 1 30 0" fill="none" stroke="#fff" stroke-width="4"/><rect x="8" y="22" width="8" height="12" rx="2" fill="#fff"/><rect x="38" y="22" width="8" height="12" rx="2" fill="#fff"/><path d="M42 34q0 6-10 7" stroke="#fff" stroke-width="3" fill="none"/><rect x="10" y="42" width="34" height="10" rx="4" fill="#fff"/></svg></div>

<div class="abs svc left" style="left:82px;top:1150px"><h3>Audio Visual<br>Installation &amp; Service</h3><p>Ut wisi enim ad minim veniam, quispi<br>[+]....&nbsp; nostrud exerci tation ullamco</p></div>
<div class="abs svc right" style="left:789px;top:1150px"><h3>Computer Systems<br>And Networks</h3><p>Ut wisi enim ad minim veniam, quispi<br>nostrud exerci tation ullamco ....[+]</p></div>
<div class="abs svc left" style="left:82px;top:1384px"><h3>Cloud Services<br>of Data Backup</h3><p>Ut wisi enim ad minim veniam, quispi<br>[+]....&nbsp; nostrud exerci tation ullamco</p></div>
<div class="abs svc right" style="left:789px;top:1384px"><h3>Support<br>Services</h3><p>Ut wisi enim ad minim veniam, quispi<br>nostrud exerci tation ullamco ....[+]</p></div>

<section>
  <h2 class="abs title" style="top:1587px">CLIENT <b>TESTIMONIALS</b></h2>
  <div class="abs divider" style="top:1643px"><i></i></div>
  <p class="abs quote"><span class="qmark">“</span>Lorem ipsum dolor sit amet, consectetuer adipiscing elit, sed diam nonummy nibh euismod tincidunt ut laoreet dolore magna aliquam erat volutpat. Ut wisi enim ad minim veniam, quis nostrud Lorem ipsum dolor sit amet, consectetuer adipiscing elit, sed diam nonummy nibh euismod tincidunt ut laoree.<span class="qmark">”</span></p>
  <p class="abs author">- Tavin Osler</p>
  <div class="abs client" style="left:254px;top:1884px;width:100px;height:99px" role="img" aria-label="Client portrait"></div>
  <div class="abs client" style="left:377px;top:1862px;width:134px;height:124px" role="img" aria-label="Client portrait"></div>
  <div class="abs client active" style="left:529px;top:1846px;width:140px;height:140px" role="img" aria-label="Featured client portrait"></div>
  <div class="abs client" style="left:699px;top:1867px;width:118px;height:116px" role="img" aria-label="Client portrait"></div>
  <div class="abs client" style="left:845px;top:1884px;width:101px;height:99px" role="img" aria-label="Client portrait"></div>
</section>

<footer class="abs footer"></footer>
<h4 class="abs f-head" style="left:135px;width:135px">Quick Links</h4>
<ul class="abs f-links"><li>Home</li><li>About Us</li><li>Services</li><li>Support</li><li>Contact Us</li></ul>
<div class="abs f-vr" style="left:305px"></div>
<h4 class="abs f-head" style="left:340px;width:205px">Contact Details</h4>
<div class="abs f-contact" style="top:2160px"><svg width="14" height="18" viewBox="0 0 14 18"><path d="M7 0a7 7 0 0 0-7 7c0 5 7 11 7 11s7-6 7-11a7 7 0 0 0-7-7z" fill="#fff"/><circle cx="7" cy="7" r="2.5" fill="#333"/></svg><div><strong>Brimlow OrthoLink IT</strong><br>2480 Corvan Street – Suite 12<br>Harlow Bay, MN 55990</div></div>
<div class="abs f-contact" style="top:2262px;font-size:16px;font-weight:700"><svg width="14" height="16" viewBox="0 0 14 16"><path d="M3 0c1.5 0 2.5 3 2 4l-1 1c.8 2 2.3 3.8 4.3 4.7l1-1c1-.5 3.7.5 3.7 2 0 1.5-1.3 3.3-3 3.3C5 13.6.4 9 0 3 0 1.5 1.5 0 3 0z" fill="#fff"/></svg>555.014.2290</div>
<div class="abs f-contact" style="top:2323px"><svg width="16" height="12" viewBox="0 0 16 12"><rect width="16" height="12" fill="#fff"/><path d="M0 0l8 7 8-7" fill="none" stroke="#333" stroke-width="1.5"/></svg>info@brimlowortholink.example</div>
<div class="abs f-vr" style="left:593px"></div>
<h4 class="abs f-head" style="left:626px;width:242px">Quick Inquiry</h4>
<div class="abs field" style="top:2164px">Name</div>
<div class="abs field" style="top:2197px">Email</div>
<div class="abs field" style="top:2231px">Phone</div>
<div class="abs field" style="top:2266px;height:74px">Message</div>
<div class="abs submit">SUBMIT</div>
<div class="abs f-vr" style="left:903px"></div>
<div class="abs f-brand"><i></i>Brimlow<br>OrthoLink IT</div>
<div class="abs social footer-social"><span></span><span></span><span></span></div>

<div class="abs copyright">copyright © 2016 Brimlow OrthoLink IT.&nbsp; ALL RIGHT RESERVED</div>

</body>
</html>
```